Verlindo Magician

I want the business card for my business to give to people who watch that later I will be employed to show magic here is my website http://www.balsamomagicien.com/I want the interesting design , i am very opened for formal and informal, I watch a lot of design so don't stick to the common shape and form but i hope it can also be produced the thing to write on will be the same as in picture that i will upload , i also will upload the logo for you that so can be easy to useDenis CostilleMagicianMAGICIAN BALSAMO 17 rue des Tilleuls - 25000 BESANÇON contact@verlindoillusions.example tel. 0381 946 157 tel. 0674 219 503

```html
<!DOCTYPE html>
<html lang="fr">
<head>
<meta charset="utf-8">
<title>Verlindo Magician – Business Card</title>
<link href="https://fonts.googleapis.com/css2?family=Jost:wght@300;400;500&display=swap" rel="stylesheet">
<style>
  :root {
    --page: #e9e6e1;
    --paper: #ffffff;
    --ink: #111111;
    --grey: #555555;
    --red: #e8232a;
    --card-w: 700px;
    --card-h: 400px;
  }
  * { box-sizing: border-box; margin: 0; padding: 0; }
  html, body { width: 1200px; height: 1040px; overflow: hidden; }
  body {
    background: var(--page);
    font-family: 'Jost', sans-serif;
    position: relative;
  }
  .card {
    position: absolute;
    left: 250px;
    width: var(--card-w);
    height: var(--card-h);
    overflow: hidden;
    box-shadow: 0 6px 18px rgba(0,0,0,.18);
  }
  /* Front */
  .card-front { top: 70px; background: var(--paper); }
  .portrait {
    position: absolute;
    background: linear-gradient(160deg, #2a2a2a, #050505);
    border-radius: 40% 40% 12% 12%;
  }
  .card-front .portrait { left: 60px; top: 50px; width: 200px; height: 180px; }
  .brand-name {
    position: absolute;
    left: 60px; top: 240px; width: 200px;
    text-align: center;
    font-weight: 400; font-size: 30px; letter-spacing: 2px;
    color: var(--ink);
  }
  .divider {
    position: absolute;
    left: 270px; top: 140px;
    width: 240px; height: 1px;
    background: linear-gradient(90deg, rgba(0,0,0,0), #9a9a9a 40%, rgba(0,0,0,0));
  }
  .identity { position: absolute; left: 330px; top: 42px; }
  .person-name { font-size: 30px; font-weight: 400; color: var(--ink); line-height: 1.1; }
  .person-role { font-size: 19px; font-weight: 400; color: var(--red); margin-top: 2px; }
  .details {
    position: absolute; left: 330px; top: 160px;
    list-style: none;
    font-size: 15px; font-weight: 300; color: var(--grey);
    line-height: 22px;
  }
  .details li { display: flex; align-items: center; gap: 8px; }
  .details .no-icon { padding-left: 0; }
  .details svg { width: 13px; height: 13px; flex: none; }
  .band {
    position: absolute; left: 0; top: 310px;
    width: 100%; height: 52px;
    background: var(--ink);
    display: flex; align-items: center; justify-content: space-between;
    padding: 0 28px;
  }
  .band .site { color: #fff; font-size: 19px; font-weight: 400; letter-spacing: 1.5px; }
  .suits { display: flex; gap: 6px; }
  .suits svg { width: 26px; height: 26px; }
  /* Back */
  .card-back { top: 560px; background: var(--red); }
  .card-back .portrait { left: 240px; top: 105px; width: 240px; height: 190px; }
  .back-site {
    position: absolute; left: 28px; top: 200px;
    transform: translateY(-50%) rotate(90deg);
    transform-origin: left center;
    color: #fff; font-size: 17px; letter-spacing: 1.5px; white-space: nowrap;
  }
  .back-site { left: 40px; top: 60px; transform: rotate(90deg); transform-origin: left top; }
</style>
</head>
<body>

<section class="card card-front">
  <div class="portrait" role="img" aria-label="Black and white illustration of the magician holding a playing card"></div>
  <div class="brand-name">VERLINDO</div>
  <div class="divider"></div>

  <div class="identity">
    <h1 class="person-name">Marc Ravoulet</h1>
    <p class="person-role">Magician</p>
  </div>

  <ul class="details">
    <li>MAGICIAN VERLINDO</li>
    <li>17 rue des Tilleuls - 25000 BESANÇON</li>
    <li><svg viewBox="0 0 24 24"><path fill="#111" d="M6.6 10.8a15 15 0 006.6 6.6l2.2-2.2c.3-.3.7-.4 1-.2 1.1.4 2.3.6 3.6.6.6 0 1 .4 1 1V20c0 .6-.4 1-1 1A17 17 0 013 4c0-.6.4-1 1-1h3.5c.6 0 1 .4 1 1 0 1.3.2 2.5.6 3.6.1.3 0 .7-.2 1z"/></svg>0381 946 157</li>
    <li><svg viewBox="0 0 24 24"><path fill="#111" d="M6.6 10.8a15 15 0 006.6 6.6l2.2-2.2c.3-.3.7-.4 1-.2 1.1.4 2.3.6 3.6.6.6 0 1 .4 1 1V20c0 .6-.4 1-1 1A17 17 0 013 4c0-.6.4-1 1-1h3.5c.6 0 1 .4 1 1 0 1.3.2 2.5.6 3.6.1.3 0 .7-.2 1z"/></svg>0674 219 503</li>
    <li><svg viewBox="0 0 24 24"><rect x="2" y="5" width="20" height="14" fill="#111"/><path d="M2 5l10 8 10-8" stroke="#fff" stroke-width="1.6" fill="none"/></svg>contact@verlindoillusions.example</li>
  </ul>

  <div class="band">
    <div class="suits">
      <svg viewBox="0 0 24 24"><path d="M12 2C9 7 4 9 4 14a4 4 0 007 2.5L10 22h4l-1-5.5A4 4 0 0020 14c0-5-5-7-8-12z" fill="none" stroke="#fff" stroke-width="1.5"/></svg>
      <svg viewBox="0 0 24 24"><path d="M12 1l8 11-8 11-8-11z" fill="var(--red)"/></svg>
    </div>
    <span class="site">www.verlindoillusions.example</span>
    <div class="suits">
      <svg viewBox="0 0 24 24"><path d="M12 21L3.5 12.5A5 5 0 0112 5.5a5 5 0 018.5 7z" fill="var(--red)"/></svg>
      <svg viewBox="0 0 24 24"><g fill="none" stroke="#fff" stroke-width="1.5"><circle cx="12" cy="7" r="4"/><circle cx="7" cy="14" r="4"/><circle cx="17" cy="14" r="4"/><path d="M12 14l-1.5 8h3z"/></g></svg>
    </div>
  </div>
</section>

<section class="card card-back">
  <div class="back-site">www.verlindoillusions.example</div>
  <div class="portrait" role="img" aria-label="Black and white illustration of the magician holding a playing card"></div>
</section>

</body>
</html>
```